QVR business card

Need a business card for a company that provides instructional design and elearning development services. The website is here: http://quorvane.studio/

I'm attaching a current logo, as well as the old business card design. While I like to keep it clean, the old design is too simplistic for my liking. The only idea I want to reuse from the old design is placing industry jargon on the back of the card, just need a better way to present it. But if you have other ideas for the back--feel free to experiment.

Please use the colors complementary to the color we have on the website. Thank you!

```html
<!DOCTYPE html>
<html lang="en">
<head>
<meta charset="utf-8">
<title>QVR business card</title>
<link rel="stylesheet" href="https://fonts.googleapis.com/css2?family=Nunito+Sans:wght@600;700;800&family=Roboto:wght@400;500&display=swap">
<style>
  :root {
    --backdrop: #a09e9f;
    --card-dark: #353535;
    --card-light: #f4f4f3;
    --teal: #17b19c;
    --gold: #d8cf86;
    --grey-word: #a9a9a9;
    --ink: #2a2a2a;
    --ink-soft: #3a3a3a;
  }
  * { margin: 0; padding: 0; box-sizing: border-box; }
  html, body {
    width: 1200px; height: 1200px; overflow: hidden;
    background: var(--backdrop);
  }
  .canvas { position: relative; width: 1200px; height: 1200px; }

  .card {
    position: absolute;
    width: 712px; height: 418px;
    border-radius: 24px;
    overflow: hidden;
  }

  /* Front */
  .card-front { left: 238px; top: 118px; background: var(--card-dark); }
  .headline {
    position: absolute; inset: 0;
    font-family: "Nunito Sans", sans-serif; font-weight: 700;
  }
  .headline span { position: absolute; line-height: 1; white-space: nowrap; }
  .word-how  { left: 250px; top: 100px; font-size: 78px; color: var(--gold); }
  .word-can  { left: 186px; top: 160px; font-size: 78px; color: var(--grey-word); }
  .word-we   { left: 352px; top: 172px; font-size: 50px; color: var(--teal); }
  .word-help { left: 250px; top: 222px; font-size: 82px; color: var(--gold); }
  .word-mark { left: 452px; top: 110px; font-size: 210px; color: var(--teal); font-weight: 800; }

  /* Back */
  .card-back { left: 231px; top: 643px; background: var(--card-light); }
  .side-band { position: absolute; left: 0; top: 0; width: 60px; height: 100%; background: var(--teal); }
  .side-rule { position: absolute; left: 60px; top: 0; width: 7px; height: 100%; background: var(--gold); }

  .brand-name {
    position: absolute; left: 111px; top: 52px;
    font-family: "Nunito Sans", sans-serif; font-weight: 800;
    font-size: 66px; line-height: 1; letter-spacing: 2px;
    color: var(--teal);
  }

  .person-name {
    position: absolute; left: 111px; top: 234px;
    font-family: "Nunito Sans", sans-serif; font-weight: 700;
    font-size: 25px; color: var(--ink);
  }
  .contact-list {
    position: absolute; left: 111px; top: 286px;
    list-style: none;
    font-family: "Roboto", sans-serif; font-size: 18px; color: var(--ink-soft);
  }
  .contact-list li { display: flex; align-items: center; height: 27px; }
  .contact-list svg { width: 16px; height: 16px; margin-right: 19px; fill: var(--teal); }
</style>
</head>
<body>
<main class="canvas">

  <section class="card card-front" aria-label="Card front">
    <h1 class="headline">
      <span class="word-how">How</span>
      <span class="word-can">can</span>
      <span class="word-we">we</span>
      <span class="word-help">Help</span>
      <span class="word-mark">?</span>
    </h1>
  </section>

  <section class="card card-back" aria-label="Card back">
    <div class="side-band"></div>
    <div class="side-rule"></div>

    <div class="brand-name">QVR</div>

    <p class="person-name">Mirela Ostrovan</p>
    <ul class="contact-list">
      <li>
        <svg viewBox="0 0 16 16" aria-hidden="true"><path d="M1 5c0-2 3-3 7-3s7 1 7 3v1h-3V5c-1-.5-2.5-.7-4-.7S5 4.5 4 5v1H1zM4 7h8l2 6H2z"/></svg>
        555-018-3427
      </li>
      <li>
        <svg viewBox="0 0 16 16" aria-hidden="true"><path d="M8 1a7 7 0 1 0 0 14A7 7 0 0 0 8 1zm0 1.4c.8.8 1.5 2.1 1.8 3.6H6.2C6.5 4.5 7.2 3.2 8 2.4zM2.5 7h2.6a11 11 0 0 0 0 2H2.5a5.6 5.6 0 0 1 0-2zm8.4 0h2.6a5.6 5.6 0 0 1 0 2h-2.6a11 11 0 0 0 0-2zM6.1 7h3.8a10 10 0 0 1 0 2H6.1a10 10 0 0 1 0-2zm.1 3h3.6c-.3 1.5-1 2.8-1.8 3.6-.8-.8-1.5-2.1-1.8-3.6z"/></svg>
        www.quorvane.studio
      </li>
      <li>
        <svg viewBox="0 0 16 16" aria-hidden="true"><path d="M1 3h14v10H1zm1.5 1.5v.4L8 9l5.5-4.1v-.4zm0 2.3v4.7h3.2zm11 0-3.2 4.7h3.2z"/></svg>
        mostrovan@quorvane.studio
      </li>
    </ul>
  </section>

</main>
</body>
</html>
```